Digital Marketing Website Redesign, modern, fresh, dynamic

Hi there, we would like to freshen up our website and create a new dynamic look. We are a digital marketing agency who specialise in digital transformation in the form of creating websites for appointment bookings. Our clients are service businesses such as hairdressers, dentists and doctors who's patients need to book appointments with them.

Our company name is Tallomex with the point being we can help increase your revenue curve by increasing your appointment bookings.

Our services include building the website, creating campaigns to drive traffic, increasing conversions and monitoring and reporting.

We are playing with a tagline of 'Step into your Digital Transformation' as we have a 5 step journey that customers can take with us getting them from zero to full appointment bookings.

Our current website is www.tallomex-sample.com

You can see a draft design that I mocked up on Canva here https://www.draftboard-sample.com/design/QXB82LmpR7T/KpoW39dnFsYbZet_wqe_OPa/edit?utm_content=QXB82LmpR7T&utm_campaign=designshare&utm_medium=link2&utm_source=sharebutton

Also attached some other homepage ideas. In regard to photos we are open to ideas.

Please let if you need any more information to provide us with an initial design. Thanks million and I look forward to receiving fantastic designs :)

Marian Dobbs
Tallomex

Target Market(s)

Appointment based businesses such as hairdressers, dentists, doctors

Industry/Entity Type

Marketing and Digital

Coding

Coded - Design and coding required

Number of Pages Required

1 page

Colors
0094D4
00A9DD
6FCCEA
C7EBF8
E9F6FB

Requirements
Must have
• Appointment booking CTA
Nice to have
• A website we like https://www.fergalwhitty-sample.ie

```html
<!DOCTYPE html>
<html lang="en">
<head>
<meta charset="utf-8">
<title>Tallomex – Step into your Digital Transformation</title>
<link href="https://fonts.googleapis.com/css2?family=Poppins:wght@400;500;600;700&display=swap" rel="stylesheet">
<style>
:root{
  --lime:#b4be18;
  --ink:#111111;
  --black:#000000;
  --footer:#171717;
  --white:#ffffff;
  --blue:#0a45b9;
  --card-line:#3d8fe6;
  --navy:#0b0b3a;
  --grey:#555555;
  --brand:#2a54a8;
}
*{box-sizing:border-box;margin:0;padding:0}
html,body{width:1200px;height:3933px;overflow:hidden}
body{font-family:'Poppins',sans-serif;color:var(--ink);background:var(--white);position:relative}
.abs{position:absolute}
a{color:inherit;text-decoration:none}

/* nav */
.logo{font-weight:600;font-size:19px;color:var(--brand)}
.nav-link{font-size:13px;top:52px}
.nav-cta{left:971px;top:42px;width:162px;height:34px;background:var(--lime);color:var(--white);font-size:13px;display:flex;align-items:center;justify-content:center;border-radius:2px}

/* hero */
.hero-title{left:67px;top:272px;font-size:43px;font-weight:600;line-height:60px;width:520px}
.hero-text{left:67px;top:412px;width:450px;font-size:13px;line-height:20px}
.btn-lime{background:var(--lime);color:var(--white);display:flex;align-items:center;justify-content:center;font-size:13px;border-radius:2px}
.hero-photo{left:577px;top:119px;width:623px;height:597px;background:radial-gradient(ellipse at 50% 35%,#bfe6ff 0%,#3f8fd6 30%,#163a7a 60%,#061a3a 100%);clip-path:polygon(0 35%,22% 0,100% 0,100% 100%,0 100%)}
.cut-box{background:var(--lime);color:var(--white);display:flex;flex-direction:column;align-items:center;justify-content:center;gap:14px;font-weight:500;font-size:15px;clip-path:polygon(0 0,70% 0,100% 30%,100% 100%,0 100%)}

/* stats */
.stats{left:0;top:716px;width:1200px;height:305px;background:var(--lime)}
.stat{width:260px;text-align:center;color:var(--white)}
.stat-icon{width:54px;height:54px;margin:0 auto 16px;border-radius:8px}
.stat-label{font-size:16px;font-weight:600}
.stat-num{font-size:40px;font-weight:600;margin-top:18px}

/* steps */
.steps-photo{left:0;top:1021px;width:600px;height:784px;background:linear-gradient(135deg,#3b3b3d,#8a7a6e 45%,#c9b3a2 70%,#4a4a4c);clip-path:polygon(0 0,100% 0,100% 83%,70% 100%,0 100%)}
.steps-title{left:218px;top:1380px;font-size:46px;font-weight:600;color:var(--white)}
.step-card{width:200px;height:199px;background:var(--white);border-top:3px solid var(--card-line);box-shadow:0 4px 16px rgba(0,0,0,.08);padding:24px 26px}
.step-icon{width:36px;height:32px;border-radius:6px;margin-bottom:18px}
.step-name{font-size:20px;font-weight:600;line-height:30px}

/* journey */
.journey{left:0;top:1906px;width:1200px;height:774px;background:var(--black)}
.journey-photo{left:617px;top:1805px;width:583px;height:875px;background:linear-gradient(160deg,#2b4f6e,#7fa8c8 40%,#b9d3e6 60%,#30506c);clip-path:polygon(0 11%,17% 0,100% 0,100% 100%,0 100%)}
.journey-title{left:34px;top:2000px;font-size:43px;font-weight:600;line-height:60px;color:var(--white);width:560px}
.journey-text{left:34px;top:2198px;width:555px;color:var(--white);font-size:13px;line-height:20px}
.journey-list{left:34px;top:2282px;color:var(--white);font-size:13px;line-height:27px;padding-left:18px}
.journey-note{left:34px;top:2407px;color:var(--white);font-size:17px}

/* pricing */
.pricing-title{left:0;top:2746px;width:1200px;text-align:center;font-size:42px;font-weight:600;color:var(--lime)}
.pricing-sub{left:0;top:2820px;width:1200px;text-align:center;font-size:13px}
.plan{background:var(--white);box-shadow:0 6px 28px rgba(0,0,0,.1);border-radius:6px;text-align:center;padding-top:36px}
.plan-name{font-size:22px;font-weight:500}
.plan-pay{font-size:13px;color:var(--grey);margin-top:10px}
.plan-price{font-size:46px;font-weight:500;margin-top:30px}
.plan-price small{font-size:14px;margin-left:10px}
.plan ul{list-style:none;text-align:left;margin:26px 0 0 22px;width:240px;font-size:16px;line-height:24px}
.plan li{display:flex;gap:10px;margin-bottom:11px}
.plan li svg{flex:none;margin-top:5px}
.plan-btn{display:inline-flex;align-items:center;justify-content:center;width:108px;height:34px;border-radius:7px;background:var(--navy);color:var(--white);font-size:14px;font-weight:600;margin-top:12px}
.plan--featured{background:var(--lime);color:var(--white)}
.plan--featured .plan-pay{color:var(--white)}
.plan--featured .plan-btn{background:var(--white);color:var(--ink)}

/* cta */
.cta{left:0;top:3401px;width:1200px;height:210px;background:var(--lime);text-align:center;color:var(--white)}
.cta h2{font-size:27px;font-weight:600;margin-top:35px}
.cta p{font-size:13px;margin-top:14px}
.cta a{display:inline-flex;width:134px;height:44px;background:var(--blue);align-items:center;justify-content:center;font-size:13px;margin-top:22px;border-radius:2px}

/* footer */
.footer{left:0;top:3611px;width:1200px;height:322px;background:var(--footer);color:var(--white)}
.footer h4{font-size:17px;font-weight:500}
.footer .f-col{font-size:13px;line-height:33px}
.footer-line{left:105px;top:252px;width:1034px;height:1px;background:#555}
.copyright{left:0;top:280px;width:1200px;text-align:center;font-size:13px}
</style>
</head>
<body>

<header>
  <div class="abs logo" style="left:75px;top:46px">Tallomex</div>
  <nav>
    <a class="abs nav-link" style="left:542px">5 Steps</a>
    <a class="abs nav-link" style="left:617px">Our Pricing</a>
    <a class="abs nav-link" style="left:716px">Ahead of the Curve</a>
    <a class="abs nav-link" style="left:872px">Our Team</a>
    <a class="abs nav-cta">Book an appointment</a>
  </nav>
</header>

<section>
  <h1 class="abs hero-title">Step into your Digital Transformation</h1>
  <p class="abs hero-text">Digital transfromation is a journey. At Tallomex we divide the journey into five key steps that take your business from comprehensive market research to full appointment bookings. Ready to go on that journey ?</p>
  <a class="abs btn-lime" style="left:67px;top:519px;width:133px;height:44px">Get Started</a>
  <div class="abs hero-photo" role="img" aria-label="Man walking through a glowing blue digital tunnel"></div>
  <a class="abs cut-box" style="left:499px;top:516px;width:167px;height:167px">
    <svg width="34" height="34" viewBox="0 0 34 34"><circle cx="17" cy="17" r="17" fill="#fff"/><path d="M13 10 L24 17 L13 24Z" fill="#b4be18"/></svg>
    PLAY VIDEO
  </a>
</section>

<section class="abs stats">
  <div class="abs stat" style="left:79px;top:70px">
    <div class="stat-icon" role="img" aria-label="Calendar booking icon" style="background:linear-gradient(#3bbfa0,#2a8f7c)"></div>
    <div class="stat-label">Appointments Booking</div>
    <div class="stat-num">762</div>
  </div>
  <div class="abs stat" style="left:362px;top:70px">
    <div class="stat-icon" role="img" aria-label="Marketing campaigns icon" style="background:linear-gradient(#4b6fe0,#2a3e9a)"></div>
    <div class="stat-label">Marketing Caampaigns</div>
    <div class="stat-num">31</div>
  </div>
  <div class="abs stat" style="left:649px;top:70px">
    <div class="stat-icon" role="img" aria-label="Rising traffic chart icon" style="background:linear-gradient(#f29a4a,#e35a5a)"></div>
    <div class="stat-label">Website Traffic Increase</div>
    <div class="stat-num">25</div>
  </div>
  <div class="abs stat" style="left:896px;top:70px">
    <div class="stat-icon" role="img" aria-label="Light bulb idea icon" style="background:linear-gradient(#ffd04a,#f39a1a)"></div>
    <div class="stat-label">Creative Ideas</div>
    <svg style="margin-top:16px" width="40" height="40" viewBox="0 0 40 40" fill="none" stroke="#fff" stroke-width="3" stroke-linecap="round" stroke-linejoin="round"><path d="M6 16 V12 H32"/><path d="M26 6 L32 12 L26 18"/><path d="M34 24 V28 H8"/><path d="M14 34 L8 28 L14 22"/></svg>
  </div>
</section>

<section>
  <div class="abs steps-photo" role="img" aria-label="Hands typing on a laptop with a smartwatch"></div>
  <h2 class="abs steps-title">5 Steps</h2>
  <div class="abs step-card" style="left:533px;top:1055px"><div class="step-icon" role="img" aria-label="Chat review icon" style="background:#f6c544"></div><div class="step-name">Online Readiness Review</div></div>
  <div class="abs step-card" style="left:533px;top:1290px"><div class="step-icon" role="img" aria-label="Keyword analytics icon" style="background:#4cc0b0"></div><div class="step-name">Keyword Analytics</div></div>
  <div class="abs step-card" style="left:533px;top:1522px"><div class="step-icon" role="img" aria-label="Monitoring chart icon" style="background:#f09a5a"></div><div class="step-name">Monitor and maintenance</div></div>
  <div class="abs step-card" style="left:800px;top:1157px"><div class="step-icon" role="img" aria-label="Campaign icon" style="background:#4b6fe0"></div><div class="step-name">Marketing Campaigns</div></div>
  <div class="abs step-card" style="left:800px;top:1420px"><div class="step-icon" role="img" aria-label="Calendar booking icon" style="background:#3bbfa0"></div><div class="step-name">Appointment Bookings</div></div>
</section>

<section>
  <div class="abs journey"></div>
  <div class="abs journey-photo" role="img" aria-label="Hands pointing at sticky notes on a planning wall"></div>
  <h2 class="abs journey-title">Start your journey by booking an appointment with us</h2>
  <p class="abs journey-text">Book your free, no commitment appointment with us. We can meet you for coffee in Carrowbeg (Westmara Ireland) or Altbrunn (Switzerland) or on Meetlyn. It'll take about 20 minutes and we will aim to cover the following.</p>
  <ol class="abs journey-list">
    <li>Describe your business</li>
    <li>What you need help with</li>
    <li>What are your 3 / 6 / 12 month goals ?</li>
    <li>How we can help.</li>
  </ol>
  <p class="abs journey-note">Book your appointment on the calender</p>
  <a class="abs cut-box" style="left:533px;top:2455px;width:166px;height:166px">
    <svg width="30" height="30" viewBox="0 0 30 30" fill="none" stroke="#fff" stroke-width="2.5" stroke-linecap="round" stroke-linejoin="round"><path d="M4 15 H26"/><path d="M17 6 L26 15 L17 24"/></svg>
    CHECK NOW
  </a>
</section>

<section>
  <h2 class="abs pricing-title">Our Pricing</h2>
  <p class="abs pricing-sub">which plan you take will depend on how many steps you want to take on your digital transformation journey.</p>

  <div class="abs plan" style="left:89px;top:2891px;width:311px;height:418px">
    <div class="plan-name">Starter Plan</div>
    <div class="plan-pay">Pay up front</div>
    <div class="plan-price">$399<small>/a month</small></div>
    <ul>
      <li><svg width="14" height="14" viewBox="0 0 14 14" fill="none" stroke="currentColor"><circle cx="7" cy="7" r="6"/><path d="M4 7 L6 9 L10 5"/></svg>Step 1 : Online readiness review based on our 12 point checklist</li>
      <li><svg width="14" height="14" viewBox="0 0 14 14" fill="none" stroke="currentColor"><circle cx="7" cy="7" r="6"/><path d="M4 7 L6 9 L10 5"/></svg>Step 2 : implementation</li>
      <li><svg width="14" height="14" viewBox="0 0 14 14" fill="none" stroke="currentColor"><circle cx="7" cy="7" r="6"/><path d="M4 7 L6 9 L10 5"/></svg>Lorem ipsum dolor</li>
      <li><svg width="14" height="14" viewBox="0 0 14 14" fill="none" stroke="currentColor"><circle cx="7" cy="7" r="6"/><path d="M4 7 L6 9 L10 5"/></svg>Lorem ipsum dolor</li>
    </ul>
    <a class="plan-btn">Join Now</a>
  </div>

  <div class="abs plan plan--featured" style="left:428px;top:2868px;width:345px;height:464px;padding-top:44px">
    <div class="plan-name">Premium Plan</div>
    <div class="plan-pay">Pay up front</div>
    <div class="plan-price" style="font-size:50px">$599<small>/a month</small></div>
    <ul style="margin-left:26px">
      <li><svg width="14" height="14" viewBox="0 0 14 14" fill="none" stroke="currentColor"><circle cx="7" cy="7" r="6"/><path d="M4 7 L6 9 L10 5"/></svg>Steps 1 &amp; 2</li>
      <li><svg width="14" height="14" viewBox="0 0 14 14" fill="none" stroke="currentColor"><circle cx="7" cy="7" r="6"/><path d="M4 7 L6 9 L10 5"/></svg>Step 3 : Content is King</li>
      <li><svg width="14" height="14" viewBox="0 0 14 14" fill="none" stroke="currentColor"><circle cx="7" cy="7" r="6"/><path d="M4 7 L6 9 L10 5"/></svg>Lorem ipsum dolor</li>
      <li><svg width="14" height="14" viewBox="0 0 14 14" fill="none" stroke="currentColor"><circle cx="7" cy="7" r="6"/><path d="M4 7 L6 9 L10 5"/></svg>Lorem ipsum dolor</li>
    </ul>
    <a class="plan-btn" style="width:120px;height:38px">Join Now</a>
  </div>

  <div class="abs plan" style="left:800px;top:2891px;width:311px;height:418px">
    <div class="plan-name">Ultimate Plan</div>
    <div class="plan-pay">Pay up front</div>
    <div class="plan-price">$899<small>/a month</small></div>
    <ul style="width:200px">
      <li><svg width="14" height="14" viewBox="0 0 14 14" fill="none" stroke="currentColor"><circle cx="7" cy="7" r="6"/><path d="M4 7 L6 9 L10 5"/></svg>Steps 1, 2, &amp; 3</li>
      <li><svg width="14" height="14" viewBox="0 0 14 14" fill="none" stroke="currentColor"><circle cx="7" cy="7" r="6"/><path d="M4 7 L6 9 L10 5"/></svg>Step 4 : Monitoring Campaigns</li>
      <li><svg width="14" height="14" viewBox="0 0 14 14" fill="none" stroke="currentColor"><circle cx="7" cy="7" r="6"/><path d="M4 7 L6 9 L10 5"/></svg>Step 5 : Monitor and mantanance</li>
      <li><svg width="14" height="14" viewBox="0 0 14 14" fill="none" stroke="currentColor"><circle cx="7" cy="7" r="6"/><path d="M4 7 L6 9 L10 5"/></svg>Lorem ipsum dolor</li>
    </ul>
    <a class="plan-btn" style="margin-top:0">Join Now</a>
  </div>
</section>

<section class="abs cta">
  <h2>Ready to step into your digital transformation ?</h2>
  <p>Book your free appointment with us</p>
  <a>Book Here</a>
</section>

<footer class="abs footer">
  <div class="abs logo" style="left:92px;top:80px">Tallomex</div>
  <p class="abs" style="left:83px;top:152px;width:335px;font-size:13px;line-height:20px">Lorem ipsum dolor sit amet consectetur. Varius habitant et urna molestie. Integer sollicitudin aliquet eget luctus et posuere. In nulla maecenas fermentum in nunc fames placerat eu. Turpis.</p>

  <div class="abs" style="left:486px;top:68px">
    <h4>Contact Details</h4>
    <div style="display:flex;align-items:center;gap:14px;margin-top:18px;font-size:13px">
      <svg width="20" height="20" viewBox="0 0 20 20"><circle cx="10" cy="10" r="10" fill="#fff"/><path d="M7 5 L9 8 L8 9 Q9 11 11 12 L12 11 L15 13 L14 15 Q8 15 5 7Z" fill="#171717"/></svg>01632 960418
    </div>
    <div style="display:flex;align-items:center;gap:14px;margin-top:14px;font-size:10px">
      <svg width="20" height="20" viewBox="0 0 20 20"><circle cx="10" cy="10" r="10" fill="#fff"/><rect x="5" y="6.5" width="10" height="7" fill="none" stroke="#171717"/><path d="M5 6.5 L10 10.5 L15 6.5" fill="none" stroke="#171717"/></svg>HELLO@TALLOMEX-SAMPLE.COM
    </div>
  </div>

  <div class="abs f-col" style="left:791px;top:68px">
    <h4 style="margin-bottom:6px">Quick Links</h4>
    <div>5 Steps</div><div>Our Pricing</div><div>Ahead of the Curve</div><div>Our Team</div>
  </div>

  <div class="abs f-col" style="left:1003px;top:68px">
    <h4 style="margin-bottom:6px">Customer Services</h4>
    <div>Privacy Policy</div><div>Terms and Conditions</div><div>Support</div><div>Help</div>
  </div>

  <div class="abs footer-line"></div>
  <p class="abs copyright">© 2024&nbsp; All rights reserved | Tallomex</p>
</footer>

</body>
</html>
```